kolvarin.link kolvarin.space kolvarin.press website

The website is named KOLVARIN and it will have 3 domain names. kolvarin.link, press, space.
I'd like it to be viewed on Pads, pcs and phones.

page menu:

kolvarin.link(start page): presentation of company. (creative, design, app, new product innovation.)
Here we'll need sosial media icons: plimber, vendoloop, mirtavel, trelvanet. (light but some 'fruity' colors)

kolvarin.press: blog. It will be a 75% picture blog > rest will be text. I need to be able to resize pictures and shape columns to picture size. (light but some 'fruity' colors)

kolvarin.space : the fun part of this web design, however, on entering the page I'd like a non-disclosure agreement where viewer simply click "yes, I agree" after filling out contact info. (check attached document)
We will have space here for uploading PDF files viewers can download. There is also a blog space here to tell in brief about the PDF file. (maybe a space/sci-fi theme her e.g spacechimp, Laika the space dog?)

I will attach the logo here I want you to use > and develop for the .space .press webpage. The logo i uploaded is for the .link page.

Target Market(s)

venture capitalists

Number of Pages Required

3 page

Requirements
Must have
• a few 'fruity colors' but mostly white and grey

```html
<!DOCTYPE html>
<html lang="en">
<head>
<meta charset="utf-8">
<title>Kolvarin Link</title>
<link href="https://fonts.googleapis.com/css2?family=Arimo:wght@400;700&family=Comfortaa:wght@600;700&display=swap" rel="stylesheet">
<style>
:root{
  --green:#5a9a3c;
  --green-dark:#2a7a2f;
  --green-deep:#2f6e2a;
  --red:#d9412a;
  --footer-red:#e14b33;
  --pink:#fbe1e0;
  --text:#333333;
  --muted:#666666;
  --line:#e2e2e2;
  --white:#ffffff;
}
*{box-sizing:border-box;margin:0;padding:0}
html,body{width:942px;height:1200px;overflow:hidden;background:var(--white)}
body{position:relative;font-family:"Arimo",Arial,sans-serif;color:var(--text)}
.abs{position:absolute}

/* header */
.topbar{position:absolute;left:0;top:0;width:942px;height:29px}
.contact-item{position:absolute;top:7px;font-size:11.5px;color:var(--muted);display:flex;align-items:center;gap:6px}
.social-list{position:absolute;left:788px;top:6px;display:flex;gap:6px}
.social-list span{display:block;width:17px;height:17px;background:#e2452d;border-radius:2px}
.brand{position:absolute;left:70px;top:24px;display:flex;align-items:center;gap:6px}
.brand-mark{width:14px;height:14px;background:#f2b418}
.brand-name{font-family:"Arimo",Arial,sans-serif;font-weight:700;font-size:18px;letter-spacing:.5px;color:#111}
.main-nav{position:absolute;top:29px;left:494px;height:33px;display:flex;align-items:center}
.main-nav a{font-size:11.8px;color:#333;text-decoration:none;text-align:center;position:absolute;top:0;height:33px;line-height:33px;transform:translateX(-50%)}
.main-nav .active{background:var(--green);color:#fff;width:72px;transform:none;left:0}
.nav-sep{position:absolute;top:13px;width:1px;height:9px;background:#ccc}

/* slider */
.hero{position:absolute;left:0;top:62px;width:942px;height:436px;background:linear-gradient(160deg,#6c86a6 0%,#3f5878 45%,#22344e 100%)}
.hero-corner{position:absolute;left:0;top:0}
.hero-arrow{position:absolute;top:184px;width:32px;height:26px;background:rgba(60,60,60,.85);display:flex;align-items:center;justify-content:center}
.hero-caption{position:absolute;left:0;bottom:0;width:942px;height:38px;background:rgba(40,40,40,.75);color:#fff;font-size:17.6px;text-align:center;line-height:38px}

/* section headings */
.section-title{position:absolute;left:0;width:942px;text-align:center;font-family:"Comfortaa",sans-serif;font-weight:700;font-size:26px;color:var(--green-dark)}
.section-title em{font-style:normal;color:var(--red)}
.title-rule{position:absolute;left:316px;width:320px;height:2px;background:var(--line)}
.title-rule::after{content:"";position:absolute;left:133px;top:-1px;width:53px;height:3px;background:var(--green)}

/* services */
.service{position:absolute;top:603px;width:204px;height:215px;text-align:center}
.service-card{position:absolute;left:266px;top:603px}
.service-icon{position:absolute;left:50%;top:15px;transform:translateX(-50%)}
.service h3{position:absolute;left:0;width:100%;top:121px;font-weight:400;font-size:14.6px;color:#222}
.service p{position:absolute;left:0;width:100%;top:147px;font-size:11.6px;line-height:17.6px;color:#333}
.service.is-active h3,.service.is-active p{color:#fff}
.service.is-active h3{top:119px}

/* welcome */
.welcome-text{position:absolute;left:74px;top:959px;width:794px;text-align:center;font-size:11.6px;line-height:18px;color:#333}
.welcome-text p+p{margin-top:6px}
.read-more{position:absolute;left:0;width:942px;top:1071px;text-align:center;font-size:10.5px;font-weight:700;color:#111;text-decoration:underline}

/* footer */
.footer{position:absolute;left:0;top:1128px}
.copyright{position:absolute;left:69px;top:1173px;font-size:8.8px;color:#fff}
.footer-brand{position:absolute;left:772px;top:1150px;display:flex;align-items:center;gap:5px}
.footer-brand .brand-name{font-size:15px}
</style>
</head>
<body>

<header>
  <svg class="topbar" width="942" height="29" viewBox="0 0 942 29">
    <polygon points="285,0 942,0 942,29 256,29" fill="var(--pink)"/>
    <line x1="655" y1="2" x2="655" y2="27" stroke="#fff" stroke-width="1.5"/>
    <line x1="777" y1="2" x2="777" y2="27" stroke="#fff" stroke-width="1.5"/>
  </svg>
  <div class="contact-item" style="left:510px">
    <svg width="14" height="10" viewBox="0 0 14 10"><rect width="14" height="10" rx="1" fill="#e2452d"/><polyline points="0.5,0.5 7,6 13.5,0.5" fill="none" stroke="#fbe1e0" stroke-width="1.3"/></svg>
    <span>sales@orvenda.com.au</span>
  </div>
  <div class="contact-item" style="left:664px;top:6px">
    <svg width="18" height="18" viewBox="0 0 18 18"><circle cx="9" cy="9" r="8" fill="none" stroke="#e2452d" stroke-width="1.3"/><path d="M6 4.5c-1 1.2-1 3.5.8 6s3.8 3.6 5.2 3l.9-1.3-2-1.5-1 .8c-.8-.4-2.2-2-2.5-3l.9-.9L7.4 5z" fill="#e2452d"/></svg>
    <span>(555) 018 2746</span>
  </div>
  <div class="social-list">
    <span role="img" aria-label="mirtavel"></span>
    <span role="img" aria-label="plimber"></span>
    <span role="img" aria-label="glimora"></span>
    <span role="img" aria-label="trelvanet"></span>
  </div>

  <nav class="main-nav">
    <a class="active" href="#">Home</a>
    <a href="#" style="left:108px">About</a>
    <span class="nav-sep" style="left:144px"></span>
    <a href="#" style="left:185px">Services</a>
    <span class="nav-sep" style="left:228px"></span>
    <a href="#" style="left:271px">Our Work</a>
    <span class="nav-sep" style="left:319px"></span>
    <a href="#" style="left:359px">Contact</a>
  </nav>
</header>

<section class="hero" role="img" aria-label="Businessman in a suit facing a wall of chalk sketches about ideas, growth and teamwork">
  <svg class="hero-corner" width="224" height="15" viewBox="0 0 224 15"><polygon points="0,0 224,0 208,15 0,15" fill="#fff"/></svg>
  <div class="hero-arrow" style="left:0"><svg width="10" height="12" viewBox="0 0 10 12"><polyline points="7,1 2,6 7,11" fill="none" stroke="#fff" stroke-width="2.5"/></svg></div>
  <div class="hero-arrow" style="left:910px"><svg width="10" height="12" viewBox="0 0 10 12"><polyline points="3,1 8,6 3,11" fill="none" stroke="#fff" stroke-width="2.5"/></svg></div>
  <div class="hero-caption">Lorem Ipsum Dolor Sit Amet Consectetuer Adipiscing Elit Sed Diam Nonummy Nibh</div>
</section>

<div class="brand">
  <span class="brand-mark"></span>
  <span class="brand-name">KOLVARIN</span>
</div>

<h2 class="section-title" style="top:524px">Our <em>Services</em></h2>
<div class="title-rule" style="top:557px"></div>

<svg class="service-card" width="204" height="215" viewBox="0 0 204 215">
  <polygon points="0,0 170,0 204,35 204,215 34,215 0,181" fill="var(--green)"/>
</svg>

<article class="service" style="left:58px">
  <svg class="service-icon" width="94" height="94" viewBox="0 0 94 94">
    <circle cx="47" cy="47" r="45" fill="none" stroke="var(--green)" stroke-width="3"/>
    <circle cx="47" cy="47" r="38" fill="var(--green)"/>
    <circle cx="47" cy="43" r="6" fill="#fff"/>
    <rect x="44" y="49" width="6" height="4" fill="#fff"/>
    <path d="M34 62c1-6 6-8 13-8s12 2 13 8z" fill="#fff"/>
    <g stroke="#fff" stroke-width="1.5"><line x1="47" y1="31" x2="47" y2="34"/><line x1="38" y1="35" x2="40" y2="37"/><line x1="56" y1="35" x2="54" y2="37"/></g>
  </svg>
  <h3>Creative</h3>
  <p>Lorem ipsum dolor sit amet,<br>consectetuer adipiscing elit, sed<br>diam nonummy nibh.</p>
</article>

<article class="service is-active" style="left:266px">
  <svg class="service-icon" width="94" height="94" viewBox="0 0 94 94">
    <circle cx="47" cy="47" r="45" fill="none" stroke="var(--green-deep)" stroke-width="3"/>
    <circle cx="47" cy="47" r="38" fill="var(--green-deep)"/>
    <rect x="36" y="32" width="18" height="26" rx="2" fill="none" stroke="#fff" stroke-width="2"/>
    <rect x="50" y="44" width="10" height="17" rx="2" fill="var(--green-deep)" stroke="#fff" stroke-width="2"/>
    <circle cx="45" cy="43" r="3" fill="none" stroke="#fff" stroke-width="1.5"/>
    <circle cx="31" cy="60" r="2.5" fill="#fff"/>
    <circle cx="62" cy="33" r="3" fill="#fff"/>
  </svg>
  <h3>App Development</h3>
  <p>Lorem ipsum dolor sit amet,<br>consectetuer adipiscing elit, sed<br>diam nonummy nibh.</p>
</article>

<article class="service" style="left:484px">
  <svg class="service-icon" width="94" height="94" viewBox="0 0 94 94">
    <circle cx="47" cy="47" r="45" fill="none" stroke="var(--green)" stroke-width="3"/>
    <circle cx="47" cy="47" r="38" fill="var(--green)"/>
    <circle cx="40" cy="38" r="5" fill="none" stroke="#fff" stroke-width="2.5" stroke-dasharray="2 1.5"/>
    <circle cx="51" cy="33" r="4" fill="none" stroke="#fff" stroke-width="2.5" stroke-dasharray="2 1.5"/>
    <path d="M42 48c2-4 12-4 14 2l1 6 3 3-3 1v5h-6v4h-9v-8c-3-4-2-10 0-13z" fill="#fff"/>
  </svg>
  <h3>New Product Innovations</h3>
  <p>Lorem ipsum dolor sit amet,<br>consectetuer adipiscing elit, sed<br>diam nonummy nibh.</p>
</article>

<article class="service" style="left:692px">
  <svg class="service-icon" width="94" height="94" viewBox="0 0 94 94">
    <circle cx="47" cy="47" r="45" fill="none" stroke="var(--green)" stroke-width="3"/>
    <circle cx="47" cy="47" r="38" fill="var(--green)"/>
    <rect x="30" y="34" width="34" height="22" rx="1.5" fill="none" stroke="#fff" stroke-width="2.5"/>
    <rect x="44" y="56" width="6" height="5" fill="#fff"/>
    <rect x="38" y="61" width="18" height="2.5" fill="#fff"/>
    <line x1="42" y1="50" x2="57" y2="33" stroke="#fff" stroke-width="3"/>
  </svg>
  <h3>Design</h3>
  <p>Lorem ipsum dolor sit amet,<br>consectetuer adipiscing elit, sed<br>diam nonummy nibh.</p>
</article>

<h2 class="section-title" style="top:900px">Welcome to <em>Kolvarin Link</em></h2>
<div class="title-rule" style="top:940px"></div>

<div class="welcome-text">
  <p>Lorem ipsum dolor sit amet, consectetuer adipiscing elit, sed diam nonummy nibh euismod tincidunt ut laoreet dolore magna aliquam erat volutpat. Ut wisi enim ad minim veniam, quis nostrud exerci tation ullamcorper suscipit lobortis nisl ut aliquip ex ea commodo consequat. Duis autem vel eum iriure dolor in hendrerit in vulputate velit esse molestie consequat, vel illum dolore eu feugiat nulla facilisis at vero eros et accumsan et iusto odio dignissim qui blandit praesent luptatum zzril delenit augue duis dolore te feugait nulla facilisi.</p>
  <p>We are committed to providing our customers with quality products, designs and 100% Work Satisfaction</p>
</div>
<a class="read-more" href="#">Read More</a>

<footer>
  <svg class="footer" width="942" height="72" viewBox="0 0 942 72">
    <polygon points="0,24 712,24 734,2 942,2 942,72 0,72" fill="var(--green)"/>
    <polygon points="0,28 714,28 736,5 942,5 942,72 0,72" fill="var(--footer-red)"/>
  </svg>
  <p class="copyright">Copyright© 2016&nbsp; Kolvarin Link&nbsp; All rights reserved</p>
  <div class="footer-brand">
    <span class="brand-name">KOLVARIN</span>
  </div>
</footer>

</body>
</html>
```